Velmo Swinger site - new website, blogsite and merchandise point, connection to tradeva

We are a well established Swingers Club in the North east of UK and already have an existing site. www.velmo-example.co.uk, BUT we have changed our logo and our information on the site needs to be updated.

We are changing our hosting site to Nimbrashost.example ,also wanting to start a blog which is linked to the club, plus we wish to sell a small exclusive range of Velmo linked merchandise which will also be available on Tradeva.

I have attached a pdf of the majority of the content. additionally we will provide pictures and a videoclip which should be able to be viewed by pc's, lap tops and mobile phones (the whole website must be fully accessible via phone).

The new site must be able to be updated by someone with medium computer knowledge (usually me), by no means expert. Updates will generally be new pictures and written information. The site must be able to be transferred to NimbrasHost.

Velmo is one of the countries leading clubs and emphasises friendliness, fun & safety for its members, we look after you to ensure your experience is the best we can offer. We are very proud of our reputation, built up over more than 10 years.

Target Market(s)

Swingers, dreamers & fantasists, alternative lifestyle people

Coding

Coded - Design and coding required

Number of Pages Required

5+ page

Font styles to use
Sans Serif

Colors
000000
ec1f27
fbfbfb
eeeeee
eaeaea

Requirements
Must have
• website with blog attached, link to tradeva & quidlo, ability to run videoclip and picture album and must be compatable to transfer easily to Nimbrashost and be updated by non-professional (who can learn)
• Straightforward & easy to navigate
• over 18 content page with enter button
Nice to have
• sexy site
• link to chirpster maybe
• black site would be nice with red or white writing
Should not have
• children and animals in anyway shape or form

```html
<!DOCTYPE html>
<html lang="en">
<head>
<meta charset="utf-8">
<title>Velmo — Swingers Club</title>
<link rel="stylesheet" href="https://fonts.googleapis.com/css2?family=Cinzel:wght@400;500&family=Open+Sans:wght@400;600;700&display=swap">
<style>
:root{
  --black:#000000;
  --red:#ec1f27;
  --red-deep:#c8141c;
  --white:#fbfbfb;
  --light:#eeeeee;
  --grey:#eaeaea;
  --ink:#141414;
  --panel:#1b1b1b;
  --muted:#bdbdbd;
  --serif:'Cinzel', Georgia, serif;
  --sans:'Open Sans', Arial, sans-serif;
}
*{box-sizing:border-box;margin:0;padding:0}
html,body{width:1200px;height:4100px;overflow:hidden}
body{background:var(--black);color:var(--white);font-family:var(--sans);position:relative}
section,header,footer{position:relative;width:1200px;overflow:hidden}
.photo{position:absolute;inset:0}
.inner{position:relative;width:1000px;margin:0 auto}
.btn{display:inline-block;font:600 13px/1 var(--sans);letter-spacing:.5px;text-transform:uppercase;color:var(--white);padding:12px 22px;border:2px solid var(--white)}
.btn-red{background:var(--red);border-color:var(--red);padding:13px 26px}
.btn-outline-red{border-color:var(--red);color:var(--white)}
.section-title{position:relative;font:400 40px/1.1 var(--serif);text-align:center;color:var(--white)}

/* Hero */
.hero{height:533px}
.hero .photo{background:linear-gradient(180deg,#0b1526 0%,#1c2a44 40%,#3a3020 70%,#141008 100%)}
.topbar{position:absolute;top:14px;right:100px;font-size:13px;display:flex;gap:14px;align-items:center}
.topbar span{display:flex;align-items:center;gap:6px}
.nav{position:absolute;top:52px;left:100px;right:100px;display:flex;align-items:center;justify-content:space-between}
.brand{font:400 34px/1 var(--serif);letter-spacing:3px;color:var(--white)}
.menu{display:flex;gap:20px;font-size:14px;align-items:center}
.menu a{color:var(--white);text-decoration:none}
.menu a.active{color:var(--red)}
.hero-copy{position:absolute;top:160px;left:0;right:0;text-align:center}
.hero-title{font:400 76px/1 var(--serif);letter-spacing:18px}
.hero-text{font:600 21px/1.55 var(--sans);margin:26px auto 26px;width:760px}
.dots{position:absolute;top:468px;left:0;right:0;display:flex;justify-content:center;gap:8px}
.dots i{width:11px;height:11px;border-radius:50%;border:2px solid var(--white)}
.dots i.on{background:var(--white)}

/* Welcome */
.welcome{height:710px;background:var(--red)}
.welcome .photo{background:radial-gradient(ellipse at 30% 60%,rgba(0,0,0,.12),transparent 60%),linear-gradient(180deg,#e21c24,#f0242c 50%,#d9161e)}
.welcome .section-title{padding-top:84px}
.welcome-intro{width:780px;margin:26px auto 0;text-align:center;font-size:13px;line-height:2}
.features{display:grid;grid-template-columns:repeat(4,1fr);row-gap:58px;margin-top:56px}
.feature{text-align:center}
.feature svg{width:62px;height:62px;display:block;margin:0 auto 14px}
.feature h3{font:400 18px/1 var(--serif);letter-spacing:.5px;text-transform:uppercase}
.feature p{font-size:12px;line-height:1.6;width:236px;margin:12px auto 0}

/* About */
.about{height:507px}
.about .photo{background:linear-gradient(135deg,#241010,#3c1a14 45%,#1a0c0a)}
.about-media{position:absolute;left:101px;top:63px;width:404px;height:384px;border:2px solid var(--white);background:linear-gradient(160deg,#2a0d10,#7a1c22 55%,#c8323a 80%,#3a0c0e)}
.about-copy{position:absolute;left:558px;top:82px;width:540px}
.about-copy h2{font:400 34px/1.3 var(--serif)}
.about-copy p{font-size:12.5px;line-height:2;margin-top:22px}
.about-copy .btn{margin-top:22px;padding:11px 18px;font-size:11px}

/* Offers */
.offers{height:355px}
.offers .photo{background:linear-gradient(120deg,#2b2b2b,#454545 50%,#252525)}
.offer{position:absolute;top:92px;width:484px;height:213px;border:2px solid var(--white);background:rgba(10,10,10,.85);display:flex}
.offer-media{width:212px;height:100%}
.offer-body{padding:22px 20px}
.offer-body h3{font:400 18px/1 var(--serif);color:var(--red)}
.offer-body p{font-size:12.5px;line-height:1.7;margin:14px 0 18px}
.offer-body .btn{font-size:11px;padding:12px 24px}

/* Blog */
.blog{height:437px}
.blog .photo{background:linear-gradient(180deg,#3a1010,#2a0c0c 60%,#1c0808)}
.blog .section-title{padding-top:84px}
.posts{position:absolute;top:182px;left:101px;right:101px;display:grid;grid-template-columns:1fr 1fr;gap:40px}
.post{display:flex;gap:24px}
.post-media{width:180px;height:176px;border:2px solid var(--white);flex:none}
.post h3{font:400 16px/1.45 var(--serif);text-transform:uppercase}
.post-meta{font-size:11.5px;margin-top:14px;display:flex;gap:10px;align-items:center;color:var(--light)}
.post p{font-size:12px;line-height:1.7;margin-top:12px}
.post .more{display:block;font:700 11px/1 var(--sans);color:var(--red);margin-top:12px}

/* Products */
.products{height:1298px}
.products .photo{background:linear-gradient(160deg,#151515,#242424 40%,#161616 75%,#0e0e0e)}
.products .section-title{padding-top:68px}
.grid{position:absolute;top:145px;left:101px;right:101px;display:grid;grid-template-columns:repeat(4,235px);column-gap:19px;row-gap:38px}
.product-img{height:215px;background:var(--white);display:flex;align-items:center;justify-content:center;font:700 22px/1 var(--sans);color:#9a9a9a}
.product h4{font:400 13.5px/1.6 var(--sans);margin-top:28px}
.product-foot{display:flex;justify-content:space-between;align-items:center;margin-top:10px}
.price{font:700 15px/1 var(--sans);color:var(--red)}
.store{font:700 16px/1 var(--sans);color:var(--white)}

/* Footer */
.footer{height:260px;background:var(--black);border-top:3px solid var(--red)}
.contact{display:flex;justify-content:center;gap:70px;margin-top:56px;font-size:13px;align-items:center}
.contact-item{display:flex;align-items:center;gap:14px}
.ring{width:40px;height:40px;border-radius:50%;border:1.5px solid var(--white);display:flex;align-items:center;justify-content:center}
.footer-nav{display:flex;justify-content:center;gap:22px;margin-top:28px;font:600 13px/1 var(--sans)}
.rule{position:absolute;top:178px;left:101px;right:101px;border-top:1px solid #333}
.legal{position:absolute;top:206px;left:101px;right:101px;display:flex;justify-content:space-between;align-items:center;font-size:12px}
.social{display:flex;gap:8px}
.social i{width:28px;height:28px;border-radius:50%;border:1.5px solid var(--white)}
</style>
</head>
<body>

<header class="hero">
  <div class="photo" role="img" aria-label="Night view of a lit cathedral above the city skyline"></div>
  <div class="topbar">
    <span><svg width="13" height="13" viewBox="0 0 24 24" fill="#ec1f27"><path d="M6.6 10.8a15 15 0 0 0 6.6 6.6l2.2-2.2c.3-.3.7-.4 1-.2 1.1.4 2.3.6 3.6.6.6 0 1 .4 1 1V20c0 .6-.4 1-1 1A17 17 0 0 1 3 4c0-.6.4-1 1-1h3.5c.6 0 1 .4 1 1 0 1.3.2 2.5.6 3.6.1.3 0 .7-.2 1z"/></svg>0700 555 0192</span>
    <span>|</span>
    <span><svg width="13" height="11" viewBox="0 0 24 18" fill="#ec1f27"><path d="M0 0h24v18H0z"/><path d="M1 1l11 9 11-9" stroke="#fff" stroke-width="1.6" fill="none"/></svg>hello@velmo-example.co.uk</span>
  </div>
  <nav class="nav">
    <div class="brand">Velmo</div>
    <div class="menu">
      <a class="active">Home</a><a>Diary</a><a>Theme Parties</a><a>TV/TG and Admirers</a><a>Membership</a><a>FAQs</a><a>Rooms</a><a>Contact Us</a><a>Links</a>
      <svg width="15" height="15" viewBox="0 0 24 24" fill="none" stroke="#fff" stroke-width="3"><circle cx="10" cy="10" r="7"/><path d="M15 15l7 7"/></svg>
    </div>
  </nav>
  <div class="hero-copy">
    <h1 class="hero-title">VELMO</h1>
    <p class="hero-text">We are a Swingers Club in the UK Velmo is one of the countries leading clubs and emphasises friendliness, fun &amp; safety for its members.</p>
    <span class="btn">Get more info</span>
  </div>
  <div class="dots"><i class="on"></i><i></i><i></i><i></i></div>
</header>

<section class="welcome">
  <div class="photo" role="img" aria-label="Red-toned club lounge interior"></div>
  <div class="inner">
    <h2 class="section-title">Welcome to Velmo</h2>
    <p class="welcome-intro">We are the best in the North East, and have recently been voted No 2 club in the UK. We have retained the coveted title of No 1 friendliest club in the UK (in joint 1st place with our great friends "The Velvet Rooms", London).</p>
    <div class="features">
      <div class="feature">
        <svg viewBox="0 0 64 64" fill="#fff"><circle cx="44" cy="14" r="8"/><circle cx="18" cy="32" r="8"/><circle cx="44" cy="50" r="8"/><path d="M18 32L44 14M18 32l26 18" stroke="#fff" stroke-width="4"/></svg>
        <h3>Social Area</h3><p>Nam libero tempore cum solutae nobis est eligendi sert optio</p>
      </div>
      <div class="feature">
        <svg viewBox="0 0 64 64" fill="#fff"><path d="M14 18h36a12 12 0 0 1 12 12v8a10 10 0 0 1-18 6l-4-4H24l-4 4A10 10 0 0 1 2 38v-8a12 12 0 0 1 12-12z"/><path d="M12 30h12M18 24v12" stroke="#ec1f27" stroke-width="4"/><circle cx="44" cy="26" r="3" fill="#ec1f27"/><circle cx="50" cy="32" r="3" fill="#ec1f27"/></svg>
        <h3>Play Rooms</h3><p>Nam libero tempore cum solutae nobis est eligendi sert optio</p>
      </div>
      <div class="feature">
        <svg viewBox="0 0 64 64" fill="none" stroke="#fff" stroke-width="7"><path d="M12 56V30a20 20 0 0 1 40 0v26"/><path d="M4 56h14M46 56h14" stroke-width="5"/></svg>
        <h3>Rex Dungeon</h3><p>Nam libero tempore cum solutae nobis est eligendi sert optio</p>
      </div>
      <div class="feature">
        <svg viewBox="0 0 64 64" fill="#fff"><path d="M8 8h48l4 14H4z"/><path d="M10 24h44v34H10z"/><path d="M18 30h28v16H18z" fill="#ec1f27"/></svg>
        <h3>Exhibition Area</h3><p>Nam libero tempore cum solutae nobis est eligendi sert optio</p>
      </div>
      <div class="feature">
        <svg viewBox="0 0 64 64" fill="#fff"><path d="M32 4l14 12v44H18V16z"/><g fill="#ec1f27"><rect x="24" y="22" width="6" height="8"/><rect x="34" y="22" width="6" height="8"/><rect x="24" y="36" width="6" height="8"/><rect x="34" y="36" width="6" height="8"/><rect x="28" y="50" width="8" height="10"/></g></svg>
        <h3>Amsterdam Room</h3><p>Nam libero tempore cum solutae nobis est eligendi sert optio</p>
      </div>
      <div class="feature">
        <svg viewBox="0 0 64 64" fill="#fff"><path d="M32 4C24 18 14 28 14 40a18 18 0 0 0 36 0C50 28 40 18 32 4z"/></svg>
        <h3>Wet Areas</h3><p>Nam libero tempore cum solutae nobis est eligendi sert optio</p>
      </div>
      <div class="feature">
        <svg viewBox="0 0 64 64" fill="#fff"><path d="M16 6h32v54H16z"/><g fill="#ec1f27"><rect x="22" y="12" width="6" height="6"/><rect x="36" y="12" width="6" height="6"/><rect x="22" y="24" width="6" height="6"/><rect x="36" y="24" width="6" height="6"/><rect x="22" y="36" width="6" height="6"/><rect x="36" y="36" width="6" height="6"/><rect x="28" y="48" width="8" height="12"/></g></svg>
        <h3>Hotel Rooms</h3><p>Nam libero tempore cum solutae nobis est eligendi sert optio</p>
      </div>
      <div class="feature">
        <svg viewBox="0 0 64 64" fill="none" stroke="#fff" stroke-width="4"><circle cx="30" cy="36" r="20" fill="#fff"/><path d="M10 36h40M30 16v40M16 22l28 28M44 22L16 50" stroke="#ec1f27" stroke-width="2"/><path d="M44 20L58 6"/></svg>
        <h3>Crash Space</h3><p>Nam libero tempore cum solutae nobis est eligendi sert optio</p>
      </div>
    </div>
  </div>
</section>

<section class="about">
  <div class="photo" role="img" aria-label="Dim bar interior with red lighting"></div>
  <div class="about-media" role="img" aria-label="Red-lit play room with a cross frame"></div>
  <div class="about-copy">
    <h2>Velmo :: A Great<br>Place To Meet And Play!</h2>
    <p>We are the best Swingers Club in the North East, and also voted No 2 club in the UK.</p>
    <p>We have retained the coveted title of No 1 friendliest club in the UK (in joint 1st place with our great friends "The Velvet Rooms", London). This prestigious award has been given to us by a panel of mystery visitors (swingers, singles &amp; couples) working with the publication called "Nightlife Notes" a copy of which is available in reception. Please see our Frequently Asked Questions and Membership pages for more information about the club and its facilities. Velmo was established in Harbourton in 2006.</p>
    <span class="btn btn-outline-red">Read more</span>
  </div>
</section>

<section class="offers">
  <div class="photo" role="img" aria-label="Soft grey lounge interior"></div>
  <div class="offer" style="left:101px">
    <div class="offer-media" role="img" aria-label="Bedroom with patterned bedspread and red lamp" style="background:linear-gradient(150deg,#5a1a12,#8a3a22 50%,#2a1410)"></div>
    <div class="offer-body">
      <h3>Membership Fees</h3>
      <p>New members (Couples and Single guys) - (annual) £30, this now includes the next 2 visits half price.</p>
      <span class="btn btn-red">Read more</span>
    </div>
  </div>
  <div class="offer" style="left:617px">
    <div class="offer-media" role="img" aria-label="Hotel room with red wall and bed" style="background:linear-gradient(150deg,#6a2418,#a0452a 50%,#2a1410)"></div>
    <div class="offer-body">
      <h3>Membership Discounts</h3>
      <p>We discount entry and membership to support the Armed Forces (serving and retired)...</p>
      <span class="btn btn-red">Read more</span>
    </div>
  </div>
</section>

<section class="blog">
  <div class="photo" role="img" aria-label="Dark red club room"></div>
  <h2 class="section-title">Our Blog</h2>
  <div class="posts">
    <article class="post">
      <div class="post-media" role="img" aria-label="Lounge with fireplace and warm lights" style="background:linear-gradient(160deg,#2a1a10,#7a4a24 55%,#1a100a)"></div>
      <div>
        <h3>At vero eos et accusamus et iusto odio dignipra</h3>
        <div class="post-meta"><span>▦ 17/06/2017</span><span>|</span><span>Marcus</span></div>
        <p>Nam libero tempore, cum soluta nobis eligendi optio cumque nihil impedo</p>
        <span class="more">READ MORE &gt;&gt;</span>
      </div>
    </article>
    <article class="post">
      <div class="post-media" role="img" aria-label="Bar area with red walls" style="background:linear-gradient(160deg,#2a1010,#6a2420 55%,#1a0a0a)"></div>
      <div>
        <h3>At vero eos et accusamus et iusto odio dignipra</h3>
        <div class="post-meta"><span>▦ 17/06/2017</span><span>|</span><span>Marcus</span></div>
        <p>Nam libero tempore, cum soluta nobis eligendi optio cumque nihil impedo</p>
        <span class="more">READ MORE &gt;&gt;</span>
      </div>
    </article>
  </div>
</section>

<section class="products">
  <div class="photo" role="img" aria-label="Dark monochrome club interior"></div>
  <h2 class="section-title">Velmo Products</h2>
  <div class="grid">
    <div class="product"><div class="product-img">COMING SOON</div><h4>At vero eos et accusamus eiuto odio dignessimos duc.</h4><div class="product-foot"><span class="price">$20.00</span><span class="store">tradeva</span></div></div>
    <div class="product"><div class="product-img">COMING SOON</div><h4>At vero eos et accusamus eiuto odio dignessimos duc.</h4><div class="product-foot"><span class="price">$20.00</span><span class="store">tradeva</span></div></div>
    <div class="product"><div class="product-img">COMING SOON</div><h4>At vero eos et accusamus eiuto odio dignessimos duc.</h4><div class="product-foot"><span class="price">$20.00</span><span class="store">tradeva</span></div></div>
    <div class="product"><div class="product-img">COMING SOON</div><h4>At vero eos et accusamus eiuto odio dignessimos duc.</h4><div class="product-foot"><span class="price">$20.00</span><span class="store">tradeva</span></div></div>
    <div class="product"><div class="product-img">COMING SOON</div><h4>At vero eos et accusamus eiuto odio dignessimos duc.</h4><div class="product-foot"><span class="price">$20.00</span><span class="store">tradeva</span></div></div>
    <div class="product"><div class="product-img">COMING SOON</div><h4>At vero eos et accusamus eiuto odio dignessimos duc.</h4><div class="product-foot"><span class="price">$20.00</span><span class="store">tradeva</span></div></div>
    <div class="product"><div class="product-img">COMING SOON</div><h4>At vero eos et accusamus eiuto odio dignessimos duc.</h4><div class="product-foot"><span class="price">$20.00</span><span class="store">tradeva</span></div></div>
    <div class="product"><div class="product-img">COMING SOON</div><h4>At vero eos et accusamus eiuto odio dignessimos duc.</h4><div class="product-foot"><span class="price">$20.00</span><span class="store">tradeva</span></div></div>
    <div class="product"><div class="product-img">COMING SOON</div><h4>At vero eos et accusamus eiuto odio dignessimos duc.</h4><div class="product-foot"><span class="price">$20.00</span><span class="store">tradeva</span></div></div>
    <div class="product"><div class="product-img">COMING SOON</div><h4>At vero eos et accusamus eiuto odio dignessimos duc.</h4><div class="product-foot"><span class="price">$20.00</span><span class="store">tradeva</span></div></div>
    <div class="product"><div class="product-img">COMING SOON</div><h4>At vero eos et accusamus eiuto odio dignessimos duc.</h4><div class="product-foot"><span class="price">$20.00</span><span class="store">tradeva</span></div></div>
    <div class="product"><div class="product-img">COMING SOON</div><h4>At vero eos et accusamus eiuto odio dignessimos duc.</h4><div class="product-foot"><span class="price">$20.00</span><span class="store">tradeva</span></div></div>
  </div>
</section>

<footer class="footer">
  <div class="contact">
    <div class="contact-item"><span class="ring"><svg width="14" height="18" viewBox="0 0 24 32" fill="#fff"><path d="M12 0a12 12 0 0 0-12 12c0 9 12 20 12 20s12-11 12-20A12 12 0 0 0 12 0zm0 17a5 5 0 1 1 0-10 5 5 0 0 1 0 10z"/></svg></span><span>12 Harbour Row, 3rd Floor<br>Harbourton</span></div>
    <div class="contact-item"><span class="ring"><svg width="16" height="16" viewBox="0 0 24 24" fill="#fff"><path d="M6.6 10.8a15 15 0 0 0 6.6 6.6l2.2-2.2c.3-.3.7-.4 1-.2 1.1.4 2.3.6 3.6.6.6 0 1 .4 1 1V20c0 .6-.4 1-1 1A17 17 0 0 1 3 4c0-.6.4-1 1-1h3.5c.6 0 1 .4 1 1 0 1.3.2 2.5.6 3.6.1.3 0 .7-.2 1z"/></svg></span><span>0700 555 0192</span></div>
    <div class="contact-item"><span class="ring"><svg width="16" height="12" viewBox="0 0 24 18" fill="none" stroke="#fff" stroke-width="2"><rect x="1" y="1" width="22" height="16"/><path d="M1 1l11 9 11-9"/></svg></span><span>hello@velmo-example.co.uk</span></div>
  </div>
  <nav class="footer-nav"><span>HOME</span><span>DIARY</span><span>THEME PARTIES</span><span>TV/TG AND ADMIRERS</span><span>MEMBERSHIP</span><span>FAQS</span><span>ROOMS</span><span>CONTACT US</span><span>LINKS</span></nav>
  <div class="rule"></div>
  <div class="legal"><span>Copyrights © 2017, Velmo. All rights reserved.</span><div class="social"><i></i><i></i><i></i></div></div>
</footer>

</body>
</html>
```